Rebranding of WordPress website | Velmar and Co

We currently have a wordpress website www.tordelbrewhouse.com.au that we need rebranded to Velmar and Co and modernised. Velmar and Co is an import export business. The website is also linked to Shopify.The current website was created as a coffee website but will now need to have the main page then have the 3 product pages of a menu. Our New web address is www.velmarandco.com.au Our general Enquiries email is enquiries@velmarandco.com.au and we are also on Facebook and Instagram. We are looking for a clean fresh looking website, not too fussy. Black, white, natural textures.

```html
<!DOCTYPE html>
<html lang="en">
<head>
<meta charset="utf-8">
<title>Velmar &amp; Co</title>
<link rel="stylesheet" href="https://fonts.googleapis.com/css2?family=Oswald:wght@400;500;700&family=Lato:wght@400;700&display=swap">
<style>
  :root {
    --ink: #1c1819;
    --black: #111;
    --white: #fff;
    --paper: #f2f2f2;
    --field: #efefef;
    --grey-text: #8b8684;
    --footer: #241e1c;
    --rule: #3a3230;
    --hero-dark: #2a1a12;
    --hero-mid: #5b3a24;
    --hero-warm: #9a6a44;
  }
  * { box-sizing: border-box; margin: 0; padding: 0; }
  html, body { width: 1200px; height: 2866px; overflow: hidden; background: var(--white); }
  body { position: relative; font-family: "Lato", sans-serif; color: var(--ink); }
  .abs { position: absolute; }
  .display { font-family: "Oswald", sans-serif; font-weight: 700; text-transform: uppercase; color: var(--ink); }

  /* Hero */
  .hero { left: 0; top: 0; width: 1200px; height: 610px;
    background: linear-gradient(180deg, var(--hero-dark) 0%, var(--hero-mid) 55%, var(--hero-warm) 78%, #6b4328 100%); }
  .brand { display: flex; align-items: center; gap: 10px; }
  .brand-mark { width: 12px; height: 12px; background: var(--white); display: block; }
  .brand-name { font-family: "Oswald", sans-serif; font-weight: 500; color: var(--white); text-transform: uppercase; white-space: nowrap; }
  .header-brand { left: 175px; top: 68px; }
  .header-brand .brand-name { font-size: 26px; line-height: 1; }
  .nav { left: 548px; top: 36px; display: flex; gap: 32px; }
  .nav a { font-family: "Oswald", sans-serif; font-weight: 700; font-size: 13px; color: var(--white); text-decoration: none; text-transform: uppercase; }
  .nav-icons { left: 923px; top: 31px; display: flex; gap: 12px; }
  .nav-icons span { width: 28px; height: 27px; border: 2px solid var(--white); display: flex; align-items: center; justify-content: center; }
  .hero-title { left: 169px; top: 268px; font-size: 54px; line-height: 1; color: var(--white); letter-spacing: 1px; }
  .btn-outline { left: 174px; top: 363px; width: 123px; height: 34px; border: 2px solid var(--white); color: var(--white);
    font-family: "Oswald", sans-serif; font-weight: 700; font-size: 14px; display: flex; align-items: center; justify-content: center; text-transform: uppercase; }
  .hero-arrow { top: 309px; width: 33px; height: 33px; border: 1.5px solid var(--white); border-radius: 50%; display: flex; align-items: center; justify-content: center; }

  /* Welcome */
  .welcome-title { left: 171px; top: 673px; font-size: 35px; line-height: 36px; }
  .copy { font-size: 11.5px; line-height: 20.2px; color: #222; }
  .welcome-copy { left: 172px; top: 757px; width: 300px; }
  .feature-frame { left: 530px; top: 522px; width: 516px; height: 483px; background: var(--ink); padding: 24px; }
  .feature-frame .mat { width: 100%; height: 100%; background: var(--white); padding: 14px; }
  .photo-pour { width: 100%; height: 100%; background: radial-gradient(circle at 55% 45%, #3a2416 0%, #6d4a2c 35%, #b07a48 70%, #c99660 100%); }

  /* Products */
  .products-bg { left: 0; top: 1158px; width: 479px; height: 486px; background: var(--paper); }
  .products-title { left: 171px; top: 1273px; font-size: 35px; line-height: 36px; }
  .products-copy { left: 172px; top: 1357px; width: 190px; }
  .pager { display: flex; gap: 4px; }
  .pager span { width: 29px; height: 26px; border: 1.5px solid var(--ink); background: var(--white); display: flex; align-items: center; justify-content: center; }
  .product-card { top: 1254px; width: 268px; }
  .product-frame { height: 292px; background: var(--ink); padding: 11px; }
  .product-frame .mat { width: 100%; height: 100%; background: var(--white); padding: 3px; }
  .product-photo { width: 100%; height: 100%; background: linear-gradient(135deg, #3a2a20 0%, #1c1614 55%, #7a2018 100%); }
  .product-photo.blue { background: linear-gradient(160deg, #1b1b1b 0%, #111 60%, #1e6fc9 100%); }
  .product-photo.nero { background: linear-gradient(135deg, #4a3a2c 0%, #1a1614 55%, #3a3430 100%); }
  .product-name { margin-top: 18px; text-align: center; font-family: "Oswald", sans-serif; font-weight: 400; font-size: 15px; color: #333; text-transform: uppercase; }
  .product-price { margin-top: 4px; text-align: center; font-family: "Oswald", sans-serif; font-weight: 500; font-size: 18px; color: var(--ink); }

  /* Featured machine */
  .machine-frame { left: 171px; top: 1761px; width: 408px; height: 451px; border: 7px solid var(--ink); background: var(--white); padding: 22px; }
  .photo-machine { width: 100%; height: 100%; background: radial-gradient(ellipse at 50% 50%, #3d3d3d 0%, #1e1e1e 45%, #e8e8e8 75%, #fff 100%); }
  .machine-pager { left: 325px; top: 2194px; }
  .machine-title { left: 647px; top: 1846px; font-size: 34px; line-height: 1.2; }
  .price-row { left: 648px; top: 1904px; display: flex; gap: 24px; font-family: "Oswald", sans-serif; font-weight: 500; font-size: 18px; }
  .price-row .rrp { color: var(--grey-text); text-decoration: line-through; }
  .machine-copy { left: 648px; top: 1941px; width: 350px; }
  .machine-extra { left: 648px; top: 2043px; }
  .btn-solid { left: 649px; top: 2083px; width: 131px; height: 43px; background: var(--black); border: 4px solid var(--black); outline: 2px solid var(--white); outline-offset: -7px;
    color: var(--white); font-family: "Oswald", sans-serif; font-weight: 700; font-size: 15px; display: flex; align-items: center; justify-content: center; text-transform: uppercase; }

  /* VIP */
  .vip { left: 171px; top: 2298px; width: 855px; height: 106px; border: 5px solid var(--ink); }
  .vip-title { left: 199px; top: 2331px; font-size: 29px; line-height: 1.3; font-weight: 500; }
  .vip-input { left: 425px; top: 2326px; width: 482px; height: 52px; background: var(--field); font-size: 13px; color: #444; padding-left: 16px; display: flex; align-items: center; }
  .vip-btn { left: 907px; top: 2326px; width: 98px; height: 52px; background: var(--black); color: var(--white);
    font-family: "Oswald", sans-serif; font-weight: 500; font-size: 18px; display: flex; align-items: center; justify-content: center; text-transform: uppercase; }

  /* Footer */
  .footer { left: 0; top: 2454px; width: 1200px; height: 412px; background: var(--footer); }
  .footer-brand { left: 183px; top: 2628px; }
  .footer-brand .brand-name { font-size: 30px; line-height: 1; }
  .footer-col { top: 2570px; }
  .footer-col h4 { font-family: "Oswald", sans-serif; font-weight: 500; font-size: 13.5px; color: var(--white); text-transform: uppercase; letter-spacing: .3px; }
  .footer-col .dash { width: 21px; height: 3px; background: var(--white); margin: 18px 0 15px; }
  .footer-col ul { list-style: none; }
  .footer-col li { font-size: 11.5px; line-height: 20.2px; color: var(--grey-text); }
  .footer-rule { left: 172px; top: 2800px; width: 854px; height: 1px; background: var(--rule); }
  .social { left: 184px; top: 2823px; display: flex; gap: 22px; }
  .social span { width: 16px; height: 16px; border-radius: 50%; background: var(--white); display: block; }
  .copyright { left: 600px; top: 2824px; width: 426px; text-align: right; font-size: 11.5px; color: var(--white); }
  .footer-code { left: 1097px; top: 2821px; font-size: 9px; color: var(--white); }
</style>
</head>
<body>

<header>
  <div class="abs hero" role="img" aria-label="Steaming white coffee cup on a rustic wooden table beside a spilled sack of roasted coffee beans"></div>
  <div class="abs brand header-brand"><span class="brand-mark"></span><span class="brand-name">Velmar &amp; Co</span></div>
  <nav class="abs nav">
    <a href="#">Home</a><a href="#">Products</a><a href="#">Charities we support</a><a href="#">VIP Club</a>
  </nav>
  <div class="abs nav-icons">
    <span><svg width="13" height="13" viewBox="0 0 13 13"><circle cx="5.5" cy="5.5" r="4" fill="none" stroke="#fff" stroke-width="2"/><line x1="8.5" y1="8.5" x2="12" y2="12" stroke="#fff" stroke-width="2"/></svg></span>
    <span><svg width="14" height="13" viewBox="0 0 14 13"><path d="M0 1h3l2 7h7l1.5-5H4" fill="none" stroke="#fff" stroke-width="1.8"/><circle cx="6" cy="11" r="1.3" fill="#fff"/><circle cx="11" cy="11" r="1.3" fill="#fff"/></svg></span>
    <span><svg width="12" height="13" viewBox="0 0 12 13"><circle cx="6" cy="3.5" r="3" fill="#fff"/><path d="M0 13c0-4 2.5-6 6-6s6 2 6 6z" fill="#fff"/></svg></span>
  </div>
  <h1 class="abs display hero-title">Velmar &amp; Co</h1>
  <div class="abs btn-outline">Shop now</div>
  <div class="abs hero-arrow" style="left:25px"><svg width="10" height="12" viewBox="0 0 10 12"><path d="M7 1L2 6l5 5" fill="none" stroke="#fff" stroke-width="1.5"/></svg></div>
  <div class="abs hero-arrow" style="left:1149px"><svg width="10" height="12" viewBox="0 0 10 12"><path d="M3 1l5 5-5 5" fill="none" stroke="#fff" stroke-width="1.5"/></svg></div>
</header>

<section class="welcome">
  <h2 class="abs display welcome-title">Welcome to<br>Velmar &amp; Co.</h2>
  <p class="abs copy welcome-copy">Sed ut perspiciatis unde omnis iste natus error sit voluptat em accusantium doloremque laudantium, totam rem aperia m,eaque ipsa quae ab illo inventore veritatis et quasi archite cto beatae vitae dicta sunt explicabo. Nemo enim ipsam voluptatem quia voluptas sit aspernatur aut odit aut fugit, sed quia consequuntur magni dolores eos qui ratloreione voluptatem sequi nesciunt.eque porro.</p>
  <div class="abs feature-frame"><div class="mat"><div class="photo-pour" role="img" aria-label="Milk being poured from a jug into a cup of black coffee, seen from above"></div></div></div>
</section>

<section class="products">
  <div class="abs products-bg"></div>
  <h2 class="abs display products-title">Our<br>Products</h2>
  <p class="abs copy products-copy">Sed ut perspiciatis unde omnis iste natus error sit voluptatem accusan tium doloremque laudantium,otam rem aperiam,eaque ipsa quae ab illo inventore veritatis et quasi archite cto beatae vitae dicta sunt.</p>
  <div class="abs pager" style="left:172px;top:1497px">
    <span><svg width="9" height="12" viewBox="0 0 9 12"><path d="M7 1L2 6l5 5" fill="none" stroke="#1c1819" stroke-width="1.6"/></svg></span>
    <span><svg width="9" height="12" viewBox="0 0 9 12"><path d="M2 1l5 5-5 5" fill="none" stroke="#1c1819" stroke-width="1.6"/></svg></span>
  </div>
  <article class="abs product-card" style="left:382px">
    <div class="product-frame"><div class="mat"><div class="product-photo" role="img" aria-label="Red espresso coffee bag beside a hessian sack"></div></div></div>
    <p class="product-name">Luna Rosso Caffe Lunara</p><p class="product-price">$30.00</p>
  </article>
  <article class="abs product-card" style="left:676px">
    <div class="product-frame"><div class="mat"><div class="product-photo blue" role="img" aria-label="Close-up of a black and blue decaffeinated coffee bag"></div></div></div>
    <p class="product-name">Luna Blu Caffe Lunara</p><p class="product-price">$30.00</p>
  </article>
  <article class="abs product-card" style="left:968px">
    <div class="product-frame"><div class="mat"><div class="product-photo nero" role="img" aria-label="Black espresso coffee bag beside a hessian sack"></div></div></div>
    <p class="product-name">Luna Nero Caffe Lunara</p><p class="product-price">$30.00</p>
  </article>
</section>

<section class="featured">
  <div class="abs machine-frame"><div class="photo-machine" role="img" aria-label="Black and stainless steel espresso machine with built-in grinder"></div></div>
  <div class="abs pager machine-pager">
    <span><svg width="9" height="12" viewBox="0 0 9 12"><path d="M7 1L2 6l5 5" fill="none" stroke="#1c1819" stroke-width="1.6"/></svg></span>
    <span><svg width="9" height="12" viewBox="0 0 9 12"><path d="M2 1l5 5-5 5" fill="none" stroke="#1c1819" stroke-width="1.6"/></svg></span>
  </div>
  <h2 class="abs display machine-title">The Crema Pro</h2>
  <div class="abs price-row"><span>$762.29</span><span class="rrp">$899.00 RRP</span></div>
  <p class="abs copy machine-copy">Create great tasting espresso - from bean to espresso. The Crema Pro allows you to grind the beans right before extraction, and its interchangeable filters and a choice of automatic or manual operation ensure authentic cafe style results in no time at all.</p>
  <p class="abs copy machine-extra">FREE 1 x 1kg bag of Italian Espresso Coffee</p>
  <div class="abs btn-solid">Shop now</div>
</section>

<section class="vip-club">
  <div class="abs vip"></div>
  <h2 class="abs display vip-title">Join our VIP club</h2>
  <div class="abs vip-input">Email Address:</div>
  <div class="abs vip-btn">Sign up</div>
</section>

<footer>
  <div class="abs footer"></div>
  <div class="abs brand footer-brand"><span class="brand-mark"></span><span class="brand-name">Velmar &amp; Co</span></div>
  <div class="abs footer-col" style="left:415px"><h4>Links</h4><div class="dash"></div><ul><li>Search</li><li>Contact Us</li><li>Charities</li><li>We Support</li></ul></div>
  <div class="abs footer-col" style="left:572px"><h4>Company</h4><div class="dash"></div><ul><li>About Us</li><li>Product Reviews</li><li>Privacy Policy</li><li>Terms &amp; Conditions</li><li>Discount Policies</li><li>Advanced Search</li></ul></div>
  <div class="abs footer-col" style="left:741px"><h4>My Account</h4><div class="dash"></div><ul><li>My Account</li><li>Order History</li><li>Wish List</li><li>Gifts</li><li>Wholesale</li><li>In stores</li></ul></div>
  <div class="abs footer-col" style="left:913px"><h4>Customer Care</h4><div class="dash"></div><ul><li>Order Info</li><li>Shipping / Tracking Info</li><li>Returns Info</li><li>Request Exchange</li><li>Guarantee</li></ul></div>
  <div class="abs footer-rule"></div>
  <div class="abs social" aria-label="Social links"><span></span><span></span><span></span><span></span></div>
  <p class="abs copyright">Copyright © 2019 All Rights reserved. support@velmarandco.coffee</p>
  <p class="abs footer-code">C4</p>
</footer>

</body>
</html>
```